Audio/ Video Packaging Design for a Technology company.

We need a packaging design for a bag that is 7" wide and 10" high. The design will be for a new line of audio/video products. We would like to see designs that represent a superior quality product that provides a pure connection. We want the equivalent of a nice retail bag that you would find in a store like Tallow Mart. It should be a maximum of three colors. We really want something sharp, professional and eye catching, not whimsical or cartoonish. I've included a couple of examples below. I don't really like the designs of the bags, but I want you to see examples of what I'm looking for.

The company logo, which is uploaded, should be on the design. The words "audio and video products" should be either underneath the logo or to the side. Also, somewhere on the bag, we would like the words "For a Pure Connection"

The winner of this contest will likely get the opportunity for additional work as we have more products ready to launch.

Target Market(s)

resellers, consumers - men 25-60

Industry/Entity Type

It Company

Requirements
Must have
• It should be a maximum of three colors. We really want something sharp, professional and eye catching, not whimsical or cartoonish
Nice to have
• Eye-catching design. Utilize the entire bag but don't make it too busy.
Should not have
• Whimsical, cartoonish

```html
<!DOCTYPE html>
<html lang="en">
<head>
<meta charset="utf-8">
<title>Veranto Cable Packaging</title>
<link href="https://fonts.googleapis.com/css2?family=Montserrat:wght@400;500;600;700&display=swap" rel="stylesheet">
<style>
  :root {
    --backdrop: #d9dadc;
    --card-white: #ffffff;
    --card-dark: #333538;
    --brand-ink: #2b2f36;
    --sky-blue: #4ccff5;
    --royal-blue: #2a6fd6;
    --text-light: #ffffff;
    --text-muted: #8a8c90;
    --window-light: #e6e7e9;
    --window-dark: #8e9094;
  }
  html, body {
    margin: 0;
    padding: 0;
    width: 1200px;
    height: 960px;
    overflow: hidden;
    background: var(--backdrop);
    font-family: "Montserrat", sans-serif;
  }
  .board {
    position: relative;
    width: 1200px;
    height: 960px;
  }
  .package {
    position: absolute;
    top: 206px;
    width: 482px;
    height: 712px;
  }
  .package--retail { left: 58px; }
  .package--power { left: 650px; }
  .package svg { display: block; }
  .brand-name { font-weight: 500; letter-spacing: 1px; }
  .brand-line { font-weight: 500; letter-spacing: 2px; }
  .quote { font-weight: 500; }
  .origin { font-weight: 500; letter-spacing: 1px; }
  .product-title { font-weight: 700; }
</style>
</head>
<body>
<main class="board">

  <!-- Retail package -->
  <section class="package package--retail">
    <svg width="482" height="712" viewBox="0 0 482 712">
      <defs>
        <clipPath id="retail-shape"><rect width="482" height="712" rx="30"/></clipPath>
        <linearGradient id="retail-window" x1="0" y1="0" x2="1" y2="1">
          <stop offset="0" stop-color="var(--window-dark)"/>
          <stop offset="0.45" stop-color="var(--window-light)"/>
          <stop offset="1" stop-color="var(--window-dark)"/>
        </linearGradient>
      </defs>
      <g clip-path="url(#retail-shape)">
        <rect class="card-face" width="482" height="712" fill="var(--card-white)"/>
        <rect class="hang-hole" x="185" y="28" width="112" height="42" rx="21" fill="var(--text-muted)"/>
        <rect role="img" aria-label="Circuit board trace decoration" x="0" y="110" width="92" height="160" fill="#eeeff1"/>
        <rect role="img" aria-label="Circuit board trace decoration" x="390" y="40" width="92" height="230" fill="#eeeff1"/>
        <rect role="img" aria-label="Coiled power cable with connector seen through the window" x="94" y="142" width="292" height="330" rx="24" fill="url(#retail-window)"/>
        <polygon class="accent-white-line" points="0,284 294,488 482,218 482,230 294,500 0,296" fill="var(--card-white)"/>
        <polygon class="accent-band" points="0,254 294,458 482,190 482,218 294,484 0,280" fill="var(--sky-blue)"/>
        <polygon class="dark-base" points="0,296 294,500 482,230 482,712 0,712" fill="var(--card-dark)"/>
        <polygon points="0,284 294,488 482,218 482,226 294,496 0,292" fill="var(--card-white)"/>
        <text class="brand-name" x="472" y="590" text-anchor="end" font-size="46" fill="var(--text-light)">VERANTO</text>
        <text class="brand-line" x="472" y="613" text-anchor="end" font-size="17" fill="var(--sky-blue)">audio and video products</text>
        <text class="quote" x="472" y="672" text-anchor="end" font-size="24" fill="var(--text-light)">“For a Pure Connection”</text>
        <text class="origin" transform="translate(26,676) rotate(-90)" font-size="9" fill="var(--text-muted)">MADE IN CHINA</text>
      </g>
    </svg>
  </section>

  <!-- Power cable package -->
  <section class="package package--power">
    <svg width="482" height="712" viewBox="0 0 482 712">
      <defs>
        <clipPath id="power-shape"><rect width="482" height="712" rx="30"/></clipPath>
        <linearGradient id="power-window" x1="0" y1="0" x2="1" y2="1">
          <stop offset="0" stop-color="var(--window-light)"/>
          <stop offset="0.5" stop-color="#f6f6f7"/>
          <stop offset="1" stop-color="var(--window-dark)"/>
        </linearGradient>
      </defs>
      <g clip-path="url(#power-shape)">
        <rect class="card-face" width="482" height="712" fill="var(--card-white)"/>
        <rect class="hang-hole" x="184" y="28" width="114" height="42" rx="21" fill="var(--text-muted)"/>
        <text class="brand-name" x="241" y="152" text-anchor="middle" font-size="46" fill="var(--brand-ink)">VERANTO</text>
        <text class="brand-line" x="241" y="185" text-anchor="middle" font-size="17" fill="var(--royal-blue)">audio and video products</text>
        <rect role="img" aria-label="Coiled USB cable seen through the window" x="82" y="223" width="312" height="300" rx="24" fill="url(#power-window)"/>
        <polygon class="accent-band" points="0,306 282,550 482,238 482,264 282,574 0,332" fill="var(--royal-blue)"/>
        <polygon class="dark-base" points="0,344 282,590 482,276 482,712 0,712" fill="var(--card-dark)"/>
        <polygon points="0,334 282,580 482,266 482,276 282,590 0,344" fill="var(--card-white)"/>
        <rect class="power-tag" x="26" y="542" width="28" height="104" fill="var(--sky-blue)"/>
        <text transform="translate(49,642) rotate(-90)" font-size="23" font-weight="600" fill="var(--card-dark)">POWER</text>
        <text transform="translate(80,646) rotate(-90)" font-size="19" font-weight="500" fill="var(--text-light)">110V ~300V</text>
        <text class="product-title" x="90" y="644" font-size="74" fill="var(--sky-blue)">CABLE</text>
        <rect x="60" y="650" width="320" height="2" fill="var(--royal-blue)"/>
        <text class="quote" x="210" y="681" text-anchor="middle" font-size="20" fill="var(--text-light)">“For a Pure Connection”</text>
        <text class="origin" transform="translate(466,664) rotate(-90)" font-size="9" fill="var(--text-muted)">MADE IN CHINA</text>
      </g>
    </svg>
  </section>

</main>
</body>
</html>
```